design a construction company business card

Design business card around our logo. Card must have all the typical info: name, title, address, phone, email, business name, etc. Somewhere on the card I would like to see our motto "Grounded in trust... Driven by dedication." Consider adding a splash of bright orange to the card to complement the blues and silvers/grays in the logo. We are open to metallic inks, textures, etc. We would like to see options on both light and dark backgrounds. The font in the logo is Euro Technic Extended Regular.

```html
<!DOCTYPE html>
<html lang="en">
<head>
<meta charset="utf-8">
<title>Kestrel Building Co. – Business Card</title>
<link rel="stylesheet" href="https://fonts.googleapis.com/css2?family=Roboto:ital,wght@0,300;0,400;0,500;1,400&display=swap">
<style>
  :root {
    --backdrop: #1f1f21;
    --metal-light: #f4f5f6;
    --metal-mid: #d9dadc;
    --metal-dark: #b9bbbe;
    --brand-blue: #2a3f9c;
    --accent-blue: #1f6fc4;
    --strip-grey: #8d8e91;
    --text-grey: #5e5f62;
    --rule: #4a4b4e;
  }
  * { margin: 0; padding: 0; box-sizing: border-box; }
  html, body {
    width: 1125px; height: 1200px; overflow: hidden;
    background: var(--backdrop);
    font-family: "Roboto", sans-serif;
  }
  .card {
    position: absolute;
    left: 171px;
    width: 826px;
    height: 471px;
    background:
      repeating-linear-gradient(90deg, rgba(255,255,255,0.18) 0 1px, rgba(0,0,0,0.03) 1px 3px, rgba(255,255,255,0.08) 3px 5px),
      linear-gradient(180deg, var(--metal-dark) 0%, var(--metal-light) 38%, var(--metal-light) 55%, var(--metal-mid) 100%);
    box-shadow: 0 6px 18px rgba(0,0,0,0.55);
    overflow: hidden;
  }
  .card--front { top: 106px; }
  .card--back { top: 639px; }

  .side-strip { position: absolute; left: 0; top: 0; width: 30px; height: 100%; }

  .wordmark { line-height: 1; }
  .wordmark__name { display: flex; align-items: center; gap: 12px; font-size: 62px; font-weight: 500; letter-spacing: 3px; color: var(--brand-blue); }
  .wordmark__square { width: 16px; height: 16px; background: var(--brand-blue); flex: none; }
  .wordmark__sub { font-size: 19px; font-weight: 400; letter-spacing: 4px; margin-top: 6px; color: var(--text-grey); }

  .card--front .wordmark { position: absolute; left: 82px; top: 142px; }

  .person { position: absolute; right: 52px; top: 252px; text-align: right; }
  .person__name { color: var(--brand-blue); font-size: 30px; font-weight: 500; letter-spacing: 0.5px; }
  .person__title { color: var(--text-grey); font-size: 19px; letter-spacing: 0.5px; margin-top: 4px; }

  .divider { position: absolute; left: 82px; right: 52px; top: 335px; height: 1px; background: var(--rule); }

  .contact-list { position: absolute; left: 82px; top: 354px; list-style: none; }
  .contact-list li { display: flex; align-items: center; gap: 10px; height: 26px; color: var(--text-grey); font-size: 19px; font-weight: 300; }
  .contact-list svg { width: 16px; height: 16px; fill: var(--brand-blue); flex: none; }

  .address { position: absolute; right: 52px; top: 380px; text-align: right; color: var(--text-grey); font-size: 19px; font-weight: 300; line-height: 26px; }

  .card--back .wordmark { position: absolute; left: 0; right: 0; top: 243px; text-align: center; }
  .card--back .wordmark__name { justify-content: center; }
  .motto { position: absolute; left: 0; right: 0; top: 402px; text-align: center; color: var(--text-grey); font-style: italic; font-size: 19px; }
</style>
</head>
<body>

<section class="card card--front">
  <svg class="side-strip" viewBox="0 0 30 471" preserveAspectRatio="none" aria-hidden="true">
    <defs>
      <linearGradient id="stripBlue" x1="0" y1="0" x2="0" y2="1">
        <stop offset="0" stop-color="#2a3f9c"/>
        <stop offset="0.5" stop-color="#1f6fc4"/>
        <stop offset="1" stop-color="#2a3f9c"/>
      </linearGradient>
    </defs>
    <rect width="30" height="471" fill="#8d8e91"/>
    <path d="M0 172 Q12 162 30 158 L30 471 L0 471 Z" fill="#ffffff"/>
    <path d="M0 176 Q12 167 30 164 L30 471 L0 471 Z" fill="url(#stripBlue)"/>
  </svg>

  <div class="wordmark">
    <div class="wordmark__name"><span class="wordmark__square"></span>KESTREL</div>
    <div class="wordmark__sub">BUILDING CO.</div>
  </div>

  <div class="person">
    <div class="person__name">DANIEL REYES</div>
    <div class="person__title">CEO/FOUNDER</div>
  </div>

  <div class="divider"></div>

  <ul class="contact-list">
    <li>
      <svg viewBox="0 0 24 24" aria-hidden="true"><path d="M6.6 10.8a15.1 15.1 0 0 0 6.6 6.6l2.2-2.2c.3-.3.7-.4 1-.2 1.1.4 2.3.6 3.6.6.6 0 1 .4 1 1V20c0 .6-.4 1-1 1A17 17 0 0 1 3 4c0-.6.4-1 1-1h3.5c.6 0 1 .4 1 1 0 1.3.2 2.5.6 3.6.1.3 0 .7-.2 1z"/></svg>
      555 204 7781
    </li>
    <li>
      <svg viewBox="0 0 24 24" aria-hidden="true"><path d="M2 5h20v14H2z M4 7v.4l8 5 8-5V7z" fill-rule="evenodd"/></svg>
      hello@kestrelbuild.com
    </li>
    <li>
      <svg viewBox="0 0 24 24" aria-hidden="true"><circle cx="12" cy="12" r="10"/></svg>
      www.kestrelbuild.com
    </li>
  </ul>

  <div class="address">2140 Cedar Ridge Road<br>Juneau, Alaska 99801</div>
</section>

<section class="card card--back">
  <div class="wordmark">
    <div class="wordmark__name"><span class="wordmark__square"></span>KESTREL</div>
    <div class="wordmark__sub">BUILDING CO.</div>
  </div>
  <p class="motto">Grounded in trust... Driven by dedication.</p>
</section>

</body>
</html>
```